Business Card Design needed for start up company Halvora

In need of a new business card designed for a start up company based in Sydney, Halvora is a new start up innovative Company, our mission it to make property accessible for everyday Australian and to become the leading Real Estate platform in Australia. We want it to be fresh and clean.

Industry/Entity Type

Financial

Contact Information for Business Card

Section for Name
Section for Title

HALVORA - The Strength of Pooling
Mobile:
Direct:

Font styles to use
Sans Serif

Colors
33a6d7
0692cd
0255a3
ffffff

Requirements
Must have
• Logo, all business card details

```html
<!DOCTYPE html>
<html lang="en">
<head>
<meta charset="utf-8">
<title>Halvora Business Card</title>
<link rel="stylesheet" href="https://fonts.googleapis.com/css2?family=Open+Sans:wght@400;600;700;800&display=swap">
<style>
  :root {
    --sky: #33a6d7;
    --blue: #0692cd;
    --royal: #0255a3;
    --navy: #1e4483;
    --white: #ffffff;
    --paper: #f4f5f6;
    --ink: #3a3d42;
    --backdrop: #2c2d30;
  }
  * { box-sizing: border-box; margin: 0; padding: 0; }
  html, body {
    width: 1200px; height: 960px; overflow: hidden;
    background: var(--backdrop);
    font-family: "Open Sans", Arial, sans-serif;
  }
  .canvas {
    position: relative; width: 1200px; height: 960px;
  }
  .card {
    position: absolute; left: 250px; width: 700px; height: 400px;
    overflow: hidden;
  }
  .card--front {
    top: 50px;
    background: linear-gradient(160deg, var(--sky), var(--blue));
  }
  .card--back {
    top: 510px;
    background: var(--paper);
  }
  .front-logo {
    position: absolute; left: 0; right: 0; top: 140px;
    display: flex; justify-content: center; align-items: center; gap: 18px;
  }
  .logo-dot {
    width: 74px; height: 74px; border-radius: 50%;
  }
  .front-logo .logo-dot { background: var(--white); }
  .logo-name {
    font-family: "Open Sans", Arial, sans-serif;
    font-weight: 800; font-size: 62px; letter-spacing: 1px; line-height: 1;
  }
  .front-logo .logo-name { color: var(--white); }
  .front-tagline {
    position: absolute; left: 0; right: 0; top: 262px; text-align: center;
    color: var(--white); font-size: 17px; font-weight: 400;
  }
  .wave { position: absolute; inset: 0; }
  .holder {
    position: absolute; right: 40px; top: 112px; text-align: right; color: var(--white);
  }
  .holder-name { font-size: 22px; font-weight: 700; letter-spacing: 0.5px; }
  .holder-title { font-size: 19px; font-weight: 400; }
  .back-logo {
    position: absolute; left: 44px; top: 120px;
    display: flex; align-items: center; gap: 14px;
  }
  .back-logo .logo-dot { background: var(--sky); width: 66px; height: 66px; }
  .back-logo .logo-name { color: var(--navy); font-size: 54px; }
  .contact-list {
    position: absolute; left: 44px; top: 218px; list-style: none;
    color: var(--ink); font-size: 17px; line-height: 25px;
  }
  .contact-item { display: flex; align-items: center; gap: 10px; }
  .contact-icon { width: 14px; height: 14px; fill: var(--navy); flex: none; }
  .address {
    position: absolute; right: 40px; bottom: 34px; text-align: right;
    color: var(--ink); font-size: 19px; line-height: 25px;
  }
</style>
</head>
<body>
<main class="canvas">
  <section class="card card--front" aria-label="Card front">
    <div class="front-logo">
      <span class="logo-dot"></span>
      <span class="logo-name">HALVORA</span>
    </div>
    <p class="front-tagline">The Strength of Pooling</p>
  </section>

  <section class="card card--back" aria-label="Card back">
    <svg class="wave" viewBox="0 0 700 400" preserveAspectRatio="none" aria-hidden="true">
      <path d="M0,0 H700 V232 C590,228 500,185 410,120 C320,55 180,22 0,34 V0 Z" fill="var(--navy)"/>
      <path d="M0,40 C180,28 320,62 410,128 C500,192 590,234 700,240" fill="none" stroke="var(--blue)" stroke-width="6"/>
      <path d="M0,46 C180,34 320,68 410,134 C500,198 590,240 700,246" fill="none" stroke="var(--white)" stroke-width="3"/>
    </svg>

    <div class="holder">
      <p class="holder-name">MARCUS ELLERY</p>
      <p class="holder-title">CEO/FOUNDER</p>
    </div>

    <div class="back-logo">
      <span class="logo-dot"></span>
      <span class="logo-name">HALVORA</span>
    </div>

    <ul class="contact-list">
      <li class="contact-item">
        <svg class="contact-icon" viewBox="0 0 16 16" aria-hidden="true"><path d="M2 4c0-2 2-3 3-3l2 3-2 2c1 2 3 4 5 5l2-2 3 2c0 1-1 3-3 3C7 14 2 9 2 4z"/></svg>
        <span>612 480 3175</span>
      </li>
      <li class="contact-item">
        <svg class="contact-icon" viewBox="0 0 16 16" aria-hidden="true"><path d="M4 0h8v16H4z M5.5 2v10h5V2z"/></svg>
        <span>614 552 9027</span>
      </li>
      <li class="contact-item">
        <svg class="contact-icon" viewBox="0 0 16 16" aria-hidden="true"><path d="M1 3h14v10H1z M2 4l6 5 6-5" /></svg>
        <span>marcus@halvora.com.au</span>
      </li>
      <li class="contact-item">
        <svg class="contact-icon" viewBox="0 0 16 16" aria-hidden="true"><circle cx="8" cy="8" r="7"/></svg>
        <span>www.halvora.com.au</span>
      </li>
    </ul>

    <address class="address">
      42 Harbour Street<br>Sydney, NSW 2000
    </address>
  </section>
</main>
</body>
</html>
```